National Mission Critical Construction Contractor needs Stationery Design to make a bold statement

We are a small commercial construction company, working primarily in mission critical facilities across the U.S.. We have exciting corporate changes going an and a new logo and office space so we need new stationery. The final design should incorporate our new logo and invoke a fresh, high-tech feel while looking simple and modern.

Industry/Entity Type

Construction

Contact Information for Business Card

We are required to list our state licensing qualifications on the back of our card.

Font styles to use
Sans Serif

Requirements
Must have
• We need to have a design for second page of stationery, envelopes both standard and with a window and for a 3 x 4 notepad.

```html
<!DOCTYPE html>
<html lang="en">
<head>
<meta charset="utf-8">
<title>Harbor Crest Construction Management – Stationery</title>
<link rel="stylesheet" href="https://fonts.googleapis.com/css2?family=Michroma&family=Arimo:wght@400;700&display=swap">
<style>
  :root {
    --backdrop: #ececed;
    --paper: #ffffff;
    --brand-blue: #36a9e1;
    --brand-blue-soft: rgba(54, 169, 225, 0);
    --brand-blue-deep: #1f78c1;
    --charcoal: #3b3b3d;
    --ink: #444448;
  }
  * { box-sizing: border-box; margin: 0; padding: 0; }
  html, body { width: 1200px; height: 937px; overflow: hidden; }
  body { background: var(--backdrop); font-family: "Arimo", Arial, sans-serif; color: var(--ink); position: relative; }

  .piece { position: absolute; background: var(--paper); overflow: hidden; }

  .accent-band {
    position: absolute; left: 0; right: 0; bottom: 0;
    background: linear-gradient(to bottom, var(--brand-blue-soft) 0%, var(--brand-blue) 45%, var(--brand-blue) 100%);
  }

  .brand { display: flex; align-items: center; position: absolute; }
  .brand-mark { border-radius: 50%; border: 2px solid var(--brand-blue-deep); flex: none; }
  .brand-name { font-family: "Michroma", sans-serif; color: var(--brand-blue-deep); line-height: 1; white-space: nowrap; display: block; }
  .brand-tag { font-family: "Michroma", sans-serif; color: var(--brand-blue-deep); white-space: nowrap; display: block; }

  .web { position: absolute; font-family: "Michroma", sans-serif; color: #fff; letter-spacing: .18em; white-space: nowrap; }

  /* Letterhead */
  .letterhead { left: 185px; top: 66px; width: 388px; height: 544px; }
  .letterhead .brand { left: 16px; top: 22px; }
  .letterhead .brand-mark { width: 40px; height: 40px; margin-right: 6px; }
  .letterhead .brand-name { font-size: 14px; }
  .letterhead .brand-tag { font-size: 5.4px; margin-top: 4px; letter-spacing: .12em; }
  .letter-block { position: absolute; left: 36px; width: 296px; font-size: 5.3px; line-height: 8px; color: var(--ink); }
  .letter-block strong { font-weight: 700; }
  .letter-date { top: 141px; }
  .letter-recipient { top: 159px; }
  .letter-para-1 { top: 179px; }
  .letter-para-2 { top: 242px; }
  .letter-para-3 { top: 287px; }
  .letter-closing { top: 348px; }
  .signature { position: absolute; left: 36px; top: 364px; width: 34px; height: 22px; background: #c9c9cc; border-radius: 2px; }
  .letter-sender { top: 402px; }
  .letterhead .accent-band { height: 118px; }
  .contact-list { position: absolute; list-style: none; white-space: nowrap; }
  .contact-list li { display: flex; align-items: center; gap: 3px; }
  .contact-list li::before { content: ""; border-radius: 50%; flex: none; }
  .letterhead .contact-list { left: 226px; top: 490px; font-size: 5px; color: #fff; line-height: 8.5px; }
  .letterhead .contact-list li::before { width: 5px; height: 5px; background: #fff; }

  /* Folder */
  .folder { left: 636px; top: 40px; width: 458px; height: 576px; }
  .folder .brand { left: 40px; top: 248px; }
  .folder .brand-mark { width: 78px; height: 78px; border-width: 3px; margin-right: 24px; }
  .folder .brand-name { font-size: 23px; }
  .folder .brand-tag { font-size: 10px; margin-top: 10px; letter-spacing: .12em; }
  .folder .accent-band { height: 170px; }
  .folder .web { right: 16px; bottom: 12px; font-size: 9.5px; }

  /* Business cards */
  .card { left: 46px; width: 175px; height: 92px; }
  .card-front { top: 666px; }
  .card-back { top: 785px; }
  .card .brand { left: 8px; top: 9px; }
  .card .brand-mark { width: 18px; height: 18px; border-width: 1px; margin-right: 4px; }
  .card .brand-name { font-size: 7px; }
  .card .brand-tag { font-size: 2.8px; margin-top: 2px; letter-spacing: .08em; }
  .card .accent-band { height: 26px; }
  .card-holder { position: absolute; left: 8px; top: 44px; font-size: 5.5px; color: #333; text-transform: uppercase; }
  .card-holder small { display: block; font-size: 3.8px; text-transform: none; margin-top: 2px; }
  .card .contact-list { left: 96px; top: 38px; font-size: 3.7px; color: var(--ink); line-height: 6px; }
  .card .contact-list li::before { width: 3.5px; height: 3.5px; background: var(--charcoal); }

  /* Envelope front */
  .envelope { left: 265px; top: 672px; width: 432px; height: 208px; }
  .envelope .brand { left: 14px; top: 20px; }
  .envelope .brand-mark { width: 36px; height: 36px; margin-right: 6px; }
  .envelope .brand-name { font-size: 13px; }
  .envelope .brand-tag { font-size: 5px; margin-top: 4px; letter-spacing: .1em; }
  .envelope .accent-band { height: 90px; }
  .envelope .web { right: 20px; bottom: 10px; font-size: 8px; }

  /* Envelope back */
  .envelope-back { left: 737px; top: 672px; width: 431px; height: 208px; }
  .envelope-flap { position: absolute; left: 0; top: 0; width: 100%; height: 72px; background: var(--brand-blue); border-radius: 0 0 40px 40px; }
  .envelope-flap .web { left: 0; right: 0; top: 32px; text-align: center; font-size: 10.5px; }
</style>
</head>
<body>

<!-- Letterhead -->
<section class="piece letterhead" aria-label="Letterhead">
  <div class="brand">
    <span class="brand-mark"></span>
    <div><span class="brand-name">HARBOR CREST</span><span class="brand-tag">CONSTRUCTION MANAGEMENT</span></div>
  </div>
  <p class="letter-block letter-date">July 2, 2012</p>
  <p class="letter-block letter-recipient"><strong>Dear Cili,</strong><br>Unit 4, Ridge Road, Country Name</p>
  <p class="letter-block letter-para-1">Thank you for meeting with our team last week. We are pleased to confirm the schedule for the next phase of work and the site review planned for the coming month. Our project managers will share updated drawings, cost reports and safety plans with your staff before each milestone. We look forward to keeping the facility running without interruption while the upgrade proceeds on time and within the agreed budget.</p>
  <p class="letter-block letter-para-2">Please find the revised timeline enclosed with this letter. Our office will follow up by phone to answer any questions you may have.</p>
  <p class="letter-block letter-para-3">As discussed, the electrical and cooling work will be carried out in stages so that critical systems stay online at all times. Each stage will be reviewed by our field engineers and signed off with your facilities manager before the next begins. Weekly progress notes will be sent every Friday, and our team remains available should anything need attention on site.</p>
  <p class="letter-block letter-closing">Best Regards,</p>
  <span class="signature" role="img" aria-label="Handwritten signature"></span>
  <p class="letter-block letter-sender"><strong>Dana Whitfield</strong><br>Director<br>Unit 4, Ridge Road, Country Name</p>
  <div class="accent-band" role="img" aria-label="Decorative sweeping bands in charcoal and blue"></div>
  <ul class="contact-list">
    <li>012 555 0147</li>
    <li>012 555 0148</li>
    <li>office@harborcrestcm.com</li>
    <li>www.harborcrestcm.com</li>
    <li>18 Quarry Lane, Eastfield</li>
  </ul>
</section>

<!-- Presentation folder -->
<section class="piece folder" aria-label="Presentation folder">
  <div class="brand">
    <span class="brand-mark"></span>
    <div><span class="brand-name">HARBOR CREST</span><span class="brand-tag">CONSTRUCTION MANAGEMENT</span></div>
  </div>
  <div class="accent-band" role="img" aria-label="Decorative sweeping bands in charcoal and blue"></div>
  <span class="web">www.harborcrestcm.com</span>
</section>

<!-- Business card front -->
<section class="piece card card-front" aria-label="Business card front">
  <div class="brand">
    <span class="brand-mark"></span>
    <div><span class="brand-name">HARBOR CREST</span><span class="brand-tag">CONSTRUCTION MANAGEMENT</span></div>
  </div>
  <p class="card-holder">Owen Marsh<small>Managing Director</small></p>
  <ul class="contact-list">
    <li>012 555 0147</li>
    <li>012 555 0148</li>
    <li>owen@harborcrestcm.com</li>
    <li>www.harborcrestcm.com</li>
    <li>18 Quarry Lane, Eastfield</li>
  </ul>
  <div class="accent-band" role="img" aria-label="Decorative sweeping bands in charcoal and blue"></div>
</section>

<!-- Business card back -->
<section class="piece card card-back" aria-label="Business card back">
  <div class="brand">
    <span class="brand-mark"></span>
    <div><span class="brand-name">HARBOR CREST</span><span class="brand-tag">CONSTRUCTION MANAGEMENT</span></div>
  </div>
  <div class="accent-band" role="img" aria-label="Decorative sweeping bands in charcoal and blue"></div>
</section>

<!-- Envelope front -->
<section class="piece envelope" aria-label="Envelope front">
  <div class="brand">
    <span class="brand-mark"></span>
    <div><span class="brand-name">HARBOR CREST</span><span class="brand-tag">CONSTRUCTION MANAGEMENT</span></div>
  </div>
  <div class="accent-band" role="img" aria-label="Decorative sweeping bands in charcoal and blue"></div>
  <span class="web">www.harborcrestcm.com</span>
</section>

<!-- Envelope back -->
<section class="piece envelope-back" aria-label="Envelope back">
  <div class="envelope-flap">
    <span class="web">www.harborcrestcm.com</span>
  </div>
</section>

</body>
</html>
```